Post storm repair flyer

looking for an eye catching 6x9 postcard to send out to single family home owners advertising a "Post Storm Repair Special" explaining that after the recent hurricanes its very important to have your roof checked and any repairs fixed right away before they become a bigger more costly problem and that even though your home wasn't directly hit by the storm the high wind gust could've cause unseen damage.
offer $200 off any repair *some rules may apply
Crest Roofing
877.512.DUNE
www.DuneRoofingco.example

```html
<!DOCTYPE html>
<html lang="en">
<head>
<meta charset="utf-8">
<title>Crest Roofing – Post-Storm Repair Special Postcard</title>
<link href="https://fonts.googleapis.com/css2?family=Bebas+Neue&family=Montserrat:wght@400;500;700;800&display=swap" rel="stylesheet">
<style>
:root{
  --canvas:#d4d5d7;
  --gold:#e8b021;
  --black:#000000;
  --white:#ffffff;
  --ink:#111111;
  --rule:#7a7a7a;
  --sky-top:#3b3f4d;
  --sky-mid:#4a5566;
  --roof:#2e3a4c;
  --ground:#1e2419;
}
*{margin:0;padding:0;box-sizing:border-box}
html,body{width:1200px;height:918px;overflow:hidden;background:var(--canvas)}
body{position:relative;font-family:"Montserrat",sans-serif}

.postcard{position:absolute;top:146px;width:415px;height:623px;overflow:hidden}
.postcard--front{left:164px;background:var(--roof)}
.postcard--back{left:620px;background:var(--white)}

/* front */
.storm-photo{position:absolute;inset:0;
  background:linear-gradient(180deg,var(--sky-top) 0%,var(--sky-mid) 28%,var(--roof) 52%,#3a4658 70%,var(--ground) 100%)}
.brand-name{position:absolute;top:112px;left:0;width:100%;text-align:center;
  color:var(--white);font-weight:500;font-size:17px;letter-spacing:.5px}
.headline{position:absolute;top:166px;left:0;width:100%;text-align:center;
  font-weight:800;font-size:45px;line-height:43px;color:var(--white)}
.headline .accent{color:var(--gold)}
.intro-band{position:absolute;top:309px;left:0;width:100%;height:57px;
  background:rgba(232,176,33,.72);display:flex;align-items:center;justify-content:center}
.intro-band p{width:260px;text-align:center;font-size:11.4px;line-height:14px;color:var(--ink)}
.offer-box{position:absolute;top:388px;left:24px;width:182px;height:139px;
  border:5px solid var(--gold);background:var(--black);text-align:center}
.offer-amount{font-family:"Bebas Neue",sans-serif;font-size:94px;line-height:80px;
  color:var(--gold);margin-top:12px}
.offer-terms{font-family:"Bebas Neue",sans-serif;font-size:30px;line-height:28px;color:var(--white)}
.offer-copy{position:absolute;top:416px;left:215px;width:190px;color:var(--white);
  font-size:13.4px;line-height:16.2px}
.offer-copy strong{display:block;color:var(--gold);font-weight:800;font-size:14.5px}
.call-band{position:absolute;top:547px;left:0;width:100%;height:48px;background:var(--gold);
  display:flex;align-items:center;justify-content:center;font-size:25px;color:var(--ink)}
.call-band b{font-weight:800;margin-left:7px}
.web-band{position:absolute;top:595px;left:0;width:100%;height:28px;background:var(--black);
  display:flex;align-items:center;justify-content:center;color:var(--white);
  font-size:9.5px;letter-spacing:2px}

/* back */
.back-title{position:absolute;top:26px;left:0;width:100%;text-align:center;
  font-weight:800;font-size:26px;line-height:24px;color:var(--black)}
.back-copy{position:absolute;top:84px;left:50px;width:315px;text-align:center;
  font-size:13px;line-height:16.4px;color:var(--ink)}
.back-copy strong{color:var(--gold);font-weight:800;font-size:16px}
.contact-band{position:absolute;top:151px;left:0;width:100%;height:95px;background:var(--black)}
.contact-brand{position:absolute;top:0;left:22px;height:95px;width:80px;display:flex;
  align-items:center;color:var(--gold);font-weight:800;font-size:13px;line-height:15px}
.contact-phone{position:absolute;top:14px;left:110px;width:280px;text-align:center;
  color:var(--gold);font-weight:800;font-size:34px;line-height:40px}
.contact-web{position:absolute;top:60px;left:110px;width:280px;text-align:center;
  color:var(--white);font-weight:700;font-size:12px;letter-spacing:1px}
.stamp-box{position:absolute;top:295px;left:283px;width:104px;height:116px;border:1px solid var(--rule)}
.address-line{position:absolute;left:38px;width:219px;height:0;border-top:1px solid var(--rule)}
</style>
</head>
<body>

<section class="postcard postcard--front">
  <div class="storm-photo" role="img" aria-label="Storm-damaged house roof with missing shingles, a ladder and bare trees under a dark sky"></div>
  <div class="brand-name">CREST ROOFING</div>
  <h1 class="headline"><span class="accent">POST-STORM</span><br>REPAIR<br>SPECIAL!</h1>
  <div class="intro-band">
    <p>Recent storms can cause hidden damage to your roof. Don't wait until it's too late—get a professional inspection today!</p>
  </div>
  <div class="offer-box">
    <div class="offer-amount">$200</div>
    <div class="offer-terms">OFF ANY REPAIR</div>
  </div>
  <p class="offer-copy"><strong>PROTECT YOUR HOME</strong>and avoid costly repairs by addressing storm damage early. Our expert team is ready to help!</p>
  <div class="call-band">Call now: <b>877.512.DUNE</b></div>
  <div class="web-band">www.DuneRoofingco.example</div>
</section>

<section class="postcard postcard--back">
  <h2 class="back-title">POST-STORM<br>ROOF REPAIR SPECIAL!</h2>
  <p class="back-copy"><strong>PROTECT YOUR HOME</strong> and avoid costly repairs by addressing storm damage early. Our expert team is ready to help!</p>
  <div class="contact-band">
    <div class="contact-brand">CREST ROOFING</div>
    <div class="contact-phone">877.512.DUNE</div>
    <div class="contact-web">www.DuneRoofingco.example</div>
  </div>
  <div class="stamp-box"></div>
  <div class="address-line" style="top:451px"></div>
  <div class="address-line" style="top:488px"></div>
  <div class="address-line" style="top:525px"></div>
  <div class="address-line" style="top:562px"></div>
</section>

</body>
</html>
```